New Business Card Design Project LORVANTI-Italy

we are LORVANTI-Italy
our company in the market for 3 years we are luxury cosmetic company and its about time for a facelift :)
i will like to have elegant luxurious and unique business card
that will give the person that get it a unique, luxurious and elegant impression
I'm VERY OPEN FOR NEW IDEAS , even duo i add a few files of things that i see on line and i like them

i add my logo as well
my website is LORVANTI.COM
(if you would like to see the main style that we have)

Target Market(s)

adult that have money :)

Industry/Entity Type

Business

Contact Information for Business Card

Name - Dario Lorvanti
Position - CEO and CO Founder
address - 4817 E Halvern
telephone - 555-384-1926
email - dario@lorvanti.com
fax - 555-384-1926
website - LORVANTI.COM

Colors
000000
959595
fbee3e
ffffff

Requirements
Must have
• big logo in GOLD color
• elegant look
• impressive
Nice to have
• not must but maybe classy pattern background
• not must but maybe emblem
• maybe clear plastic business card
Should not have
• colors
• images

```html
<!DOCTYPE html>
<html lang="en">
<head>
<meta charset="utf-8">
<title>LORVANTI Italy – Business Card</title>
<link rel="stylesheet" href="https://fonts.googleapis.com/css2?family=Cormorant+Garamond:wght@500&family=Barlow+Condensed:wght@400;500&display=swap">
<style>
  :root {
    --backdrop: #121212;
    --card: #2b2a2b;
    --card-edge: #1c1c1c;
    --gold: #d9ad2b;
    --white: #f2f2f2;
    --grey: #959595;
  }
  * { margin: 0; padding: 0; box-sizing: border-box; }
  html, body {
    width: 1200px;
    height: 800px;
    overflow: hidden;
    background: var(--backdrop);
  }
  .canvas {
    width: 1200px;
    height: 800px;
    display: flex;
    flex-direction: column;
    align-items: center;
    justify-content: center;
    gap: 40px;
  }
  .card {
    width: 620px;
    height: 354px;
    background: var(--card);
    border: 1px solid var(--card-edge);
    position: relative;
    box-shadow: 0 10px 30px rgba(0,0,0,0.5);
  }

  /* Front: wordmark */
  .card-front {
    display: flex;
    flex-direction: column;
    align-items: center;
    justify-content: center;
  }
  .brand-dot {
    width: 90px;
    height: 90px;
    border: 2px solid var(--gold);
    border-radius: 50%;
    margin-bottom: 18px;
  }
  .brand-name {
    font-family: "Cormorant Garamond", serif;
    font-weight: 500;
    font-size: 62px;
    letter-spacing: 4px;
    line-height: 1;
    color: var(--gold);
  }
  .brand-rule {
    width: 300px;
    height: 2px;
    background: var(--gold);
    margin: 10px 0 8px;
  }
  .brand-origin {
    font-family: "Cormorant Garamond", serif;
    font-weight: 500;
    font-size: 18px;
    letter-spacing: 3px;
    color: var(--gold);
  }

  /* Back: emblem area and contacts */
  .card-back {
    display: flex;
    align-items: center;
    padding: 0 48px 0 40px;
    gap: 48px;
  }
  .emblem-area {
    width: 240px;
    height: 240px;
    flex-shrink: 0;
  }
  .contact {
    font-family: "Barlow Condensed", sans-serif;
    font-weight: 400;
    color: var(--white);
    font-size: 17px;
    line-height: 1.45;
  }
  .contact-name {
    color: var(--gold);
    font-weight: 500;
    font-size: 27px;
    letter-spacing: 1.5px;
    line-height: 1.1;
    text-transform: uppercase;
  }
  .contact-role { font-size: 19px; }
  .contact-dash {
    width: 26px;
    height: 2px;
    background: var(--gold);
    margin: 14px 0;
  }
  .contact-label { margin-right: 4px; }
  .contact-web {
    color: var(--gold);
    font-weight: 500;
    font-size: 19px;
    letter-spacing: 1.5px;
  }
</style>
</head>
<body>
  <main class="canvas">
    <section class="card card-front" aria-label="Business card front">
      <div class="brand-dot"></div>
      <div class="brand-name">LORVANTI</div>
      <div class="brand-rule"></div>
      <div class="brand-origin">ITALY</div>
    </section>

    <section class="card card-back" aria-label="Business card back">
      <svg class="emblem-area" viewBox="0 0 240 240" role="img" aria-label="Gold circular brand emblem">
        <circle cx="120" cy="120" r="116" fill="none" stroke="#d9ad2b" stroke-width="3"/>
      </svg>
      <div class="contact">
        <div class="contact-name">Dario Lorvanti</div>
        <div class="contact-role">CEO &amp; CO Founder</div>
        <div class="contact-dash"></div>
        <div><span class="contact-label">A.</span>4817 E Halvern</div>
        <div><span class="contact-label">T.</span>555-384-1926&nbsp;&nbsp;<span class="contact-label">F.</span>555-384-1926</div>
        <div><span class="contact-label">E.</span>dario@lorvanti.com</div>
        <div class="contact-dash"></div>
        <div class="contact-web">WWW.LORVANTI.COM</div>
      </div>
    </section>
  </main>
</body>
</html>
```